Logo and bag for Turkish coffee brand

We are a coffee roasting company. We need a logo for our new Turkish coffee brand. We are targeting C+ to A- customer segment. Our brand is above average in pricing and can be expressed as very good in quality or a bit less than excellentOur brand name is قهواكQahwakIt is an Arabic word that means "Your coffee" and if read in a different way it means "I love You"

Target Market(s)

We are selling in Egyptian market for customer segments from C+ and up to A-

Logo Text

Binnitak بنّيتك

Requirements
Must have
• 1. The logo must contain brand name in Arabic good to have it in Arabic and English if possible.
• 2. All text content must be in Arabic and good to be in both Arabic and English
• 3. The package must include two spaces for limited text paragraphs
• an area for production date and expiry.
• 4. An area for selecting variants of the product. Our coffee has light-medium-dark roasted (فاتح - وسط - غامق)
• Plain or flavored (سادة - محوج)

```html
<!DOCTYPE html>
<html lang="ar">
<head>
<meta charset="utf-8">
<title>بنّيتك – Binnitak Turkish Coffee Pack</title>
<link rel="stylesheet" href="https://fonts.googleapis.com/css2?family=Amiri:wght@400;700&family=Roboto+Condensed:wght@400;700&display=swap">
<style>
  :root {
    --page: #f4f1ec;
    --parchment: #f3e6cc;
    --parchment-light: #faf2e2;
    --stain-soft: rgba(214, 160, 90, 0.28);
    --brown: #7a4a24;
    --brown-deep: #5b3419;
    --frame-tone: #a8723f;
    --sketch-light: #ead6b6;
    --sketch-dark: #b98d60;
    --seal: #e6a65a;
    --label-light: #fffaf2;
    --ink: #4a3422;
  }
  * { box-sizing: border-box; margin: 0; padding: 0; }
  html, body {
    width: 824px; height: 1200px; overflow: hidden;
    background: var(--page);
  }
  .canvas {
    position: relative; width: 824px; height: 1200px;
    display: flex; align-items: center; justify-content: center;
  }
  .pack {
    display: flex; height: 1000px;
    box-shadow: 0 10px 30px rgba(60, 35, 15, 0.18);
  }
  .panel {
    position: relative; height: 100%; overflow: hidden;
    background:
      radial-gradient(circle at 22% 14%, var(--stain-soft), transparent 32%),
      radial-gradient(circle at 82% 38%, var(--stain-soft), transparent 28%),
      radial-gradient(circle at 60% 88%, rgba(190, 130, 70, 0.3), transparent 30%),
      radial-gradient(circle at 15% 70%, rgba(230, 180, 110, 0.25), transparent 26%),
      linear-gradient(160deg, var(--parchment-light), var(--parchment) 55%, #efd9b4);
  }
  .pack-front { width: 470px; }
  .pack-side {
    width: 190px;
    border-left: 1px solid rgba(120, 80, 40, 0.25);
    background:
      radial-gradient(circle at 40% 20%, rgba(230, 170, 90, 0.25), transparent 30%),
      linear-gradient(180deg, var(--parchment-light), #f6ead4 60%, #f1dfc0);
  }

  /* front */
  .brand-frame {
    position: absolute; left: 25px; top: 100px; width: 420px; height: 380px;
  }
  .brand-frame svg { position: absolute; inset: 0; }
  .brand-name {
    position: absolute; inset: 0;
    display: flex; flex-direction: column; align-items: center; justify-content: center;
    font-family: "Amiri", serif; font-weight: 700; color: var(--brown);
    text-align: center; line-height: 1;
  }
  .brand-name .latin { font-size: 84px; }
  .brand-name .arabic { font-size: 70px; margin-top: 6px; margin-left: 90px; }
  .landmark-art {
    position: absolute; left: 30px; top: 470px; width: 300px; height: 330px;
    border-radius: 45% 45% 20% 20% / 35% 35% 15% 15%;
    background: radial-gradient(ellipse at 50% 60%, var(--sketch-dark) 0%, var(--sketch-light) 55%, transparent 78%);
    opacity: 0.75;
  }
  .variant {
    position: absolute;
    font-family: "Amiri", serif; font-weight: 400;
    color: var(--label-light); line-height: 1;
    text-shadow: 0 0 5px var(--brown), 0 0 2px var(--brown-deep), 0 2px 3px var(--brown-deep);
  }
  .variant-flavour { left: 45px; top: 805px; font-size: 62px; }
  .variant-roast { left: 280px; top: 830px; font-size: 74px; }

  /* side */
  .seal {
    position: absolute; left: 25px; top: 360px; width: 140px; height: 180px;
    border-radius: 50%;
    background: radial-gradient(ellipse, rgba(230, 166, 90, 0.45), rgba(230, 166, 90, 0.15) 70%);
    border: 3px solid var(--seal);
  }
  .ingredients {
    position: absolute; left: 16px; right: 16px; top: 580px;
    font-family: "Roboto Condensed", sans-serif; font-size: 10.5px; line-height: 1.45;
    color: var(--ink); text-align: center;
  }
  .ingredients p + p { margin-top: 6px; }
  .ingredients b { font-weight: 700; }
  .date-area {
    position: absolute; left: 22px; right: 22px; top: 745px; height: 44px;
    border: 1px solid var(--frame-tone); border-radius: 4px;
    display: flex; flex-direction: column; justify-content: space-evenly; padding: 0 10px;
  }
  .date-area span { display: block; height: 1px; background: rgba(168, 114, 63, 0.5); }
  .side-brand {
    position: absolute; left: 15px; right: 15px; top: 830px; height: 120px;
    border: 2px solid var(--frame-tone); border-radius: 40px;
    display: flex; flex-direction: column; align-items: center; justify-content: center;
    font-family: "Amiri", serif; font-weight: 700; color: var(--brown); line-height: 1.1;
  }
  .side-brand .latin { font-size: 28px; }
  .side-brand .arabic { font-size: 26px; }
</style>
</head>
<body>
  <main class="canvas">
    <div class="pack">
      <section class="panel pack-front">
        <div class="brand-frame">
          <svg viewBox="0 0 420 380" aria-hidden="true">
            <path d="M60 70 Q110 20 160 50 Q210 15 260 50 Q310 20 360 70 Q410 120 385 190 Q410 260 360 310 Q310 360 260 330 Q210 365 160 330 Q110 360 60 310 Q10 260 35 190 Q10 120 60 70 Z"
                  fill="rgba(255,250,240,0.45)" stroke="var(--frame-tone)" stroke-width="5"/>
          </svg>
          <div class="brand-name">
            <span class="latin">Binnitak</span>
            <span class="arabic">بنّيتك</span>
          </div>
        </div>
        <div class="landmark-art" role="img" aria-label="Sepia sketch of a domed mosque with minarets"></div>
        <p class="variant variant-flavour">سادة</p>
        <p class="variant variant-roast">وسط</p>
      </section>

      <aside class="panel pack-side">
        <div class="seal" role="img" aria-label="Round quality seal"></div>
        <div class="ingredients">
          <p><b>İçindekiler:</b> %100 Arabica kahve · <b>Türü:</b> Coffee Arabica · <b>Tipi:</b> Orta kavrulmuş · <b>Derecesi:</b> İnce</p>
          <p><b>Ingredients:</b> Ground Coffee 100% · <b>Variety:</b> Coffee Arabica · <b>Type:</b> Medium Roasted · <b>Degree:</b> Fine Ground</p>
        </div>
        <div class="date-area" aria-label="Production and expiry date area"><span></span><span></span></div>
        <div class="side-brand">
          <span class="latin">Binnitak</span>
          <span class="arabic">بنّيتك</span>
        </div>
      </aside>
    </div>
  </main>
</body>
</html>
```